Business Card Design For A Renovation Contractor Company

We need a business card for a new company based in Singapore, our company name is "RB Tolvane". We are a renovation contractor that builds designs into reality. We build more of F&B restaurants, retail stores and commercial offices. We work very closely with designers. The final design should communicate to our client that we are a company that you can trust, that will plan and complete your project without giving you a headache. I like my client to remember my company as "RB". The beauty of SIMPLE is important.

Industry/Entity Type

Contractor

Requirements
Nice to have
• Black or Red base

```html
<!DOCTYPE html>
<html lang="en">
<head>
<meta charset="utf-8">
<title>RB Tolvane — Business Card</title>
<link href="https://fonts.googleapis.com/css2?family=Questrial&family=Source+Sans+3:wght@400;700&display=swap" rel="stylesheet">
<style>
  :root {
    --backdrop: #ecebe8;
    --card: #ffffff;
    --ink: #1a1a1a;
    --ink-soft: #4a4a4a;
    --accent: #d81f26;
    --rule: #8c8c8c;
    --watermark: #efefef;
    --shadow: rgba(0, 0, 0, 0.16);
  }
  * { box-sizing: border-box; margin: 0; padding: 0; }
  html, body {
    width: 1200px; height: 720px; overflow: hidden;
    background: var(--backdrop);
  }
  .canvas { position: relative; width: 1200px; height: 720px; }

  .card {
    position: absolute;
    width: 560px; height: 320px;
    background: var(--card);
    box-shadow: 0 6px 18px var(--shadow);
    overflow: hidden;
  }
  .card--contact { left: 50px; top: 60px; }
  .card--brand { left: 590px; top: 340px; }

  .card__mark-bg {
    position: absolute;
    width: 300px; height: 300px;
    border: 34px solid var(--watermark);
    border-radius: 50%;
  }
  .card--contact .card__mark-bg { right: -110px; top: -60px; }
  .card--brand .card__mark-bg { left: -150px; top: 40px; }

  .wordmark {
    font-family: "Questrial", sans-serif;
    color: var(--ink);
    line-height: 1;
    letter-spacing: -0.5px;
    white-space: nowrap;
  }
  .tagline {
    font-family: "Questrial", sans-serif;
    color: var(--ink-soft);
    border-top: 1.5px solid var(--rule);
    letter-spacing: 0.3px;
    white-space: nowrap;
  }

  /* contact side */
  .contact__brand { position: absolute; left: 40px; top: 26px; }
  .contact__dot {
    width: 42px; height: 42px; border-radius: 50%;
    background: var(--accent); margin-bottom: 8px; margin-left: 30px;
  }
  .contact__brand .wordmark { font-size: 34px; }
  .contact__brand .tagline { font-size: 14px; padding-top: 2px; margin-top: 3px; width: 220px; }

  .person {
    position: absolute; left: 40px; top: 154px;
    font-family: "Source Sans 3", sans-serif;
  }
  .person__name { font-size: 18px; font-weight: 700; color: var(--ink); line-height: 22px; }
  .person__title { font-weight: 400; color: var(--accent); font-size: 15px; }

  .details { list-style: none; margin-top: 6px; }
  .details li {
    display: flex; align-items: center; gap: 8px;
    font-size: 14px; color: var(--ink-soft); line-height: 21px;
  }
  .details svg { width: 11px; height: 11px; flex: none; }
  .details .address { margin-top: 4px; font-size: 13.5px; }

  /* brand side */
  .brand__lockup { position: absolute; right: 46px; top: 110px; }
  .brand__lockup .wordmark { font-size: 62px; }
  .brand__lockup .tagline { font-size: 21px; padding-top: 2px; margin-top: 4px; }
  .brand__web {
    position: absolute; right: 110px; top: 236px;
    font-family: "Source Sans 3", sans-serif;
    font-size: 14px; letter-spacing: 3px; color: var(--ink-soft);
  }
</style>
</head>
<body>
<main class="canvas">

  <section class="card card--contact" aria-label="Business card, contact side">
    <div class="card__mark-bg"></div>
    <div class="contact__brand">
      <div class="contact__dot"></div>
      <div class="wordmark">RB Tolvane</div>
      <div class="tagline">plans made real, built right</div>
    </div>
    <div class="person">
      <p class="person__name">Your Name, <span class="person__title">Title</span></p>
      <ul class="details">
        <li>
          <svg viewBox="0 0 12 12"><circle cx="6" cy="6" r="6" fill="#d81f26"/><path d="M4 3.2l1.2 1.4-.6.8c.4.8 1 1.4 1.8 1.8l.8-.6 1.4 1.2-.8 1c-2 0-4.8-2.8-4.8-4.8z" fill="#fff"/></svg>
          123-456-0789
        </li>
        <li>
          <svg viewBox="0 0 12 12"><circle cx="6" cy="6" r="6" fill="#d81f26"/><rect x="4.2" y="2.6" width="3.6" height="6.8" rx="0.7" fill="#fff"/></svg>
          123-456-0789
        </li>
        <li>
          <svg viewBox="0 0 12 12"><circle cx="6" cy="6" r="6" fill="#d81f26"/><rect x="3" y="4" width="6" height="4.2" fill="#fff"/><path d="M3 4l3 2.4L9 4" stroke="#d81f26" stroke-width="0.7" fill="none"/></svg>
          info@rbtolvane.com
        </li>
        <li>
          <svg viewBox="0 0 12 12"><circle cx="6" cy="6" r="6" fill="#d81f26"/><circle cx="6" cy="6" r="3" fill="none" stroke="#fff" stroke-width="0.9"/><path d="M3 6h6M6 3v6" stroke="#fff" stroke-width="0.7"/></svg>
          www.rbtolvane.com
        </li>
        <li class="address">
          <svg viewBox="0 0 12 12"><circle cx="6" cy="6" r="6" fill="#d81f26"/><path d="M6 2.6a2.2 2.2 0 0 1 2.2 2.2C8.2 6.6 6 9.4 6 9.4S3.8 6.6 3.8 4.8A2.2 2.2 0 0 1 6 2.6z" fill="#fff"/></svg>
          Street Name, City Name, State Zip Code
        </li>
      </ul>
    </div>
  </section>

  <section class="card card--brand" aria-label="Business card, brand side">
    <div class="card__mark-bg"></div>
    <div class="brand__lockup">
      <div class="wordmark">RB Tolvane</div>
      <div class="tagline">plans made real, built right</div>
    </div>
    <p class="brand__web">www.rbtolvane.com</p>
  </section>

</main>
</body>
</html>
```